Business card for a Exhibition booth fabrication company

Hi. My company would like to change our corporate name card. We are an events and Exhibition stand builder company. We would like our corporate name card to resonate what we do. I need someone to create something unique that relates to the industry that I am in. The graphic designer should be creative to incorporate the elements of my industry and try to blend in well in the design of the card. Our aim is to ensure that we are unique and our card can look different from our competitors.
Updates

Target Market(s)

Marketing and events manager from all companies

Contact Information for Business Card

The business card should have the following details:
Name
Job Title
Email
Website

Colors

Designer to choose colors to be used in the design.

Requirements
Must have
• The card must be look something that is relevant to the service that I am providing. My website is: www.velmora-buildworks.com
• You can see my website to get more information on what service that I am doing
Nice to have
• On the back of my card, I would like to have a globe image with the incorporation of my company logo. This is to indicate that my services can be done in any part of the world.

```html
<!DOCTYPE html>
<html lang="en">
<head>
<meta charset="utf-8">
<title>Velmora Buildworks – Business Card</title>
<link href="https://fonts.googleapis.com/css2?family=Arimo:wght@400;700&family=Open+Sans:wght@400;600&display=swap" rel="stylesheet">
<style>
  :root {
    --backdrop: #1c1c1e;
    --card-green: #0a7a3a;
    --map-tint: #3f9a64;
    --silver: #c9cccf;
    --brand-red: #e61e29;
    --ink-gray: #6b6b6b;
    --divider-gray: #8a8a8a;
    --paper: #ffffff;
  }
  * { margin: 0; padding: 0; box-sizing: border-box; }
  html, body { width: 1200px; height: 960px; overflow: hidden; background: var(--backdrop); }
  .canvas { position: relative; width: 1200px; height: 960px; }

  .card { position: absolute; left: 240px; width: 720px; height: 411px; overflow: hidden; }

  /* Back side */
  .card-back { top: 50px; background: var(--card-green); }
  .world-map {
    position: absolute; left: 60px; top: 30px; width: 620px; height: 300px;
    border-radius: 40% 45% 38% 50%;
    background: radial-gradient(ellipse at center, rgba(63,154,100,0.55), rgba(63,154,100,0) 70%);
  }
  .back-brand {
    position: absolute; left: 0; right: 0; top: 170px; text-align: center;
    font-family: "Arimo", Arial, sans-serif; font-weight: 700; font-size: 30px;
    letter-spacing: 3px; color: var(--silver);
  }
  .back-web {
    position: absolute; left: 0; right: 0; top: 260px; text-align: center;
    font-family: "Open Sans", Arial, sans-serif; font-size: 19px; letter-spacing: 3px; color: var(--paper);
  }

  /* Front side */
  .card-front { top: 499px; background: var(--paper); }
  .front-brand {
    position: absolute; left: 0; top: 180px; width: 350px; text-align: center;
    font-family: "Arimo", Arial, sans-serif; font-weight: 700; font-size: 22px;
    letter-spacing: 2px; color: var(--ink-gray);
  }
  .front-divider { position: absolute; left: 344px; top: 0; width: 376px; height: 411px; }
  .contact-panel {
    position: absolute; left: 395px; top: 72px; color: var(--paper);
    font-family: "Open Sans", Arial, sans-serif;
  }
  .person-name { font-family: "Arimo", Arial, sans-serif; font-weight: 700; font-size: 24px; letter-spacing: 0.5px; }
  .person-title { font-family: "Arimo", Arial, sans-serif; font-size: 16px; margin-bottom: 18px; }
  .address { font-size: 15px; line-height: 20px; margin-bottom: 16px; }
  .contact-list { list-style: none; font-size: 16px; }
  .contact-list li { display: flex; align-items: center; height: 26px; }
  .contact-list svg { width: 16px; height: 16px; margin-right: 12px; flex: none; }
  .contact-list .web-line { padding-left: 28px; }
</style>
</head>
<body>
<main class="canvas">

  <section class="card card-back" aria-label="Card back">
    <div class="world-map" role="img" aria-label="Faint world map across the card"></div>
    <div class="back-brand">VELMORA BUILDWORKS</div>
    <div class="back-web">www.velmora-buildworks.com</div>
  </section>

  <section class="card card-front" aria-label="Card front">
    <div class="front-brand">VELMORA BUILDWORKS</div>
    <svg class="front-divider" viewBox="0 0 376 411" aria-hidden="true">
      <path d="M6 0 H376 V411 H6 V104 L-4 94 L6 84 Z" fill="var(--divider-gray)"/>
      <path d="M12 0 H376 V411 H12 V106 L0 94 L12 82 Z" fill="var(--brand-red)"/>
    </svg>
    <div class="contact-panel">
      <div class="person-name">DARREN KOWALSKI</div>
      <div class="person-title">PRESIDENT</div>
      <div class="address">Harbor Lane, Eastfield<br>Zipcode - 04821</div>
      <ul class="contact-list">
        <li>
          <svg viewBox="0 0 16 16"><path d="M3 1 L6 1 L7 5 L5 6.5 Q6.5 9.5 9.5 11 L11 9 L15 10 L15 13 Q14 15 12 15 Q2 13 1 3 Q1 1 3 1 Z" fill="#fff"/></svg>
          012-555-0148
        </li>
        <li>
          <svg viewBox="0 0 16 16"><rect x="1" y="3" width="14" height="10" fill="none" stroke="#fff" stroke-width="1.6"/><path d="M1 3 L8 9 L15 3" fill="none" stroke="#fff" stroke-width="1.6"/></svg>
          info@velmora-buildworks.com
        </li>
        <li>
          <svg viewBox="0 0 16 16"><circle cx="8" cy="8" r="6.5" fill="none" stroke="#fff" stroke-width="1.4"/><ellipse cx="8" cy="8" rx="3" ry="6.5" fill="none" stroke="#fff" stroke-width="1.2"/><path d="M1.5 8 H14.5 M2.5 4.8 H13.5 M2.5 11.2 H13.5" stroke="#fff" stroke-width="1.1"/></svg>
          www.velmora-buildworks.com
        </li>
      </ul>
    </div>
  </section>

</main>
</body>
</html>
```